Kelvaro.ch is looking for business card letterhead and envelope C5 with WOW effect

We need a strong business card for our company Kelvaro.ch, logo is available. You want a black or dark background on which the logo Stark r% 26 # 252; appears. Letterhead and envelope in C5 format should be in a similar design, but does not have to be We need a strong business card for our company Kelvaro.ch, logo is available. A black or dark background is desired, on which the logo Stark comes across. The letterhead and the envelope in C5 format should have a similar design.

Target Market(s)

Private customers as well as entrepreneurs

Contact Information for Business Card

E-mail: info@kelvaro-example.ch
Web.www.Kelvaro-example.ch
Tel: +41 ( 0 ) 79 482 6037
Adresse:
Lindenweg 14
9406 Tarnbach

Hier kann man Icons verwenden für Email,Tel und Adressse

Font styles to use
Other font styles liked:
• Dubai,bold

Colors

Designer to choose colors to be used in the design.

Requirements
Must have
• WOW effect
Nice to have
• R% 26 # 252; back business card with our service listings. - VEHICLE LABELING - SHOP WINDOW LABELING - STICKERS AND MUCH MORE ... in red color

```html
<!DOCTYPE html>
<html lang="en">
<head>
<meta charset="utf-8">
<title>Kelvaro.ch – Business Card</title>
<link rel="stylesheet" href="https://fonts.googleapis.com/css2?family=Montserrat:wght@400;500;700&display=swap">
<style>
  :root {
    --stage: #1b1b1c;
    --card: #262627;
    --yellow: #f7c518;
    --olive: #4a4320;
    --white: #f4f4f4;
    --muted: #d9d9d9;
  }
  * { box-sizing: border-box; margin: 0; padding: 0; }
  html, body { width: 1200px; height: 913px; overflow: hidden; }
  body {
    background: var(--stage);
    font-family: "Montserrat", Arial, sans-serif;
    position: relative;
  }
  .card {
    position: absolute;
    width: 560px;
    height: 320px;
    background: var(--card);
    overflow: hidden;
    box-shadow: 0 18px 40px rgba(0,0,0,.45);
  }
  .card--front { left: 50px; top: 100px; }
  .card--back { left: 590px; top: 490px; }

  /* front */
  .front-pattern {
    position: absolute;
    left: 0; top: 90px;
    width: 360px; height: 230px;
    background: linear-gradient(110deg, var(--yellow) 0%, var(--yellow) 45%, rgba(247,197,24,.55) 75%, rgba(247,197,24,0) 100%);
    clip-path: polygon(0 25%, 30% 0, 100% 10%, 90% 60%, 60% 100%, 0 100%);
  }
  .brand {
    font-weight: 700;
    letter-spacing: 1px;
    color: var(--white);
    text-transform: uppercase;
  }
  .card--front .brand {
    position: absolute;
    right: 34px; top: 40px;
    font-size: 30px;
  }
  .services {
    position: absolute;
    right: 34px; top: 88px;
    list-style: none;
    text-align: right;
    color: var(--muted);
    font-size: 11px;
    font-weight: 500;
    line-height: 1.6;
    text-transform: uppercase;
  }
  .services li::after {
    content: "";
    display: inline-block;
    width: 5px; height: 5px;
    margin-left: 7px;
    border-radius: 50%;
    background: var(--yellow);
    vertical-align: middle;
  }

  /* back */
  .back-pattern {
    position: absolute;
    right: 0; top: 0;
    width: 310px; height: 320px;
    background: linear-gradient(200deg, var(--olive) 0%, rgba(74,67,32,.75) 55%, rgba(74,67,32,0) 100%);
    clip-path: polygon(25% 0, 100% 0, 100% 85%, 60% 100%, 0 55%, 10% 20%);
  }
  .identity {
    position: absolute;
    left: 36px; top: 52px;
    display: flex;
    align-items: center;
    gap: 14px;
  }
  .identity-mark {
    width: 40px; height: 40px;
    background: var(--yellow);
  }
  .card--back .brand { font-size: 26px; }
  .person {
    position: absolute;
    left: 36px; top: 160px;
  }
  .person-name {
    color: var(--yellow);
    font-weight: 700;
    font-size: 22px;
  }
  .person-role {
    color: var(--white);
    font-size: 13px;
    font-weight: 500;
    margin-top: 2px;
  }
  .contact {
    position: absolute;
    left: 36px; top: 230px;
    list-style: none;
    color: var(--muted);
    font-size: 12px;
    line-height: 1.75;
  }
  .contact li { display: flex; align-items: center; gap: 9px; }
  .contact svg { width: 11px; height: 11px; fill: var(--yellow); flex: none; }
  .website {
    position: absolute;
    right: 30px; top: 214px;
    color: var(--yellow);
    font-size: 13px;
    font-weight: 500;
  }
</style>
</head>
<body>
  <section class="card card--front" aria-label="Business card front">
    <div class="front-pattern" role="img" aria-label="Yellow honeycomb hexagon pattern"></div>
    <p class="brand">Kelvaro.ch</p>
    <ul class="services">
      <li>Vehicle labeling</li>
      <li>Shop window labeling</li>
      <li>Stickers</li>
    </ul>
  </section>

  <section class="card card--back" aria-label="Business card back">
    <div class="back-pattern" role="img" aria-label="Faint olive honeycomb hexagon pattern"></div>
    <div class="identity">
      <span class="identity-mark"></span>
      <p class="brand">Kelvaro.ch</p>
    </div>
    <div class="person">
      <p class="person-name">Lukas Brenner</p>
      <p class="person-role">President</p>
    </div>
    <ul class="contact">
      <li>
        <svg viewBox="0 0 24 24" aria-hidden="true"><path d="M6.6 10.8a15.1 15.1 0 0 0 6.6 6.6l2.2-2.2a1 1 0 0 1 1-.25 11.4 11.4 0 0 0 3.6.57 1 1 0 0 1 1 1V20a1 1 0 0 1-1 1A17 17 0 0 1 3 4a1 1 0 0 1 1-1h3.5a1 1 0 0 1 1 1c0 1.25.2 2.45.57 3.57a1 1 0 0 1-.25 1z"/></svg>
        +41 ( 0 ) 79 482 6037
      </li>
      <li>
        <svg viewBox="0 0 24 24" aria-hidden="true"><path d="M2 5h20v14H2zm2 2v.5l8 5 8-5V7l-8 5z"/></svg>
        info@kelvaro-example.ch
      </li>
      <li>
        <svg viewBox="0 0 24 24" aria-hidden="true"><path d="M12 2a7 7 0 0 0-7 7c0 5.2 7 13 7 13s7-7.8 7-13a7 7 0 0 0-7-7zm0 9.5A2.5 2.5 0 1 1 12 6.5a2.5 2.5 0 0 1 0 5z"/></svg>
        Lindenweg 14 9406 Tarnbach
      </li>
    </ul>
    <p class="website">www.Kelvaro-example.ch</p>
  </section>
</body>
</html>
```